Contemporary Business card for Event Manager

Needed for my startup events company in Melbourne. Events I manage will be based within the fashion industry, sporting events, product launches etc. Not weddings or small dinner parties. Therfore I am after something professional and aimed at high end corporate market; but with the added emphasis on not being too conservative or boring. I am happy with a pop of colour e.g. yellow or copper foil.

Target Market(s)

fashion industry, design industry, high end sporting events e.g. Polo, Grand Prix, corporate clients,

Industry/Entity Type

Fashion

Contact Information for Business Card

side 1
Lucy Brandt (can be upper or lower case, have a feature full stop between first and surname, or at the end of the nameetc) I am open to ideas. I would also be fine with my initials or name as a logo on the front (if this is the case my full name would need to go on the second side of the card.
2nd side:
Mobile: +61 400 817 263
email: lucy.brandt@mailnest.com.au

on one side of the card:
event management | brand activation | Advisory Services

Font styles to use
Serif
Sans Serif

Requirements
Must have
• side 2 must have
• mobile number
• email address
• event management | brand activation | Advisory Services
• ** my full name (Lucy Brandt) must be on the card somewhere)
Nice to have
• 1st side
• I see the card stock being either a dark grey, light grey, natural white or black (all matt colours on unprocessed card). I see the writing being copper foil, or foil white or foil black.
• To give you a feel for me, think: contemporary, minimalist, I love line drawings, concrete, white with grey vein marble, copper, white, grey, black...yes I do like colour....yellow (but pops of colour) ;) I would like the card to look designer but 'on trend' as I deal with a lot of design and fashion clients....styles - think the sophistication and simplicity of Vireaux or urban contemporary.
• some examples of what I like. Although please don't leet this limit you...I really am happy to have something a little more urban or design focused like a line drawing of an object, person too or a photo image too.
• https://www.moodtackle.com/pin/830165427719302846/
• https://www.moodtackle.com/pin/607281935540173268/
• https://www.moodtackle.com/pin/318746205913457092/
• https://www.moodtackle.com/pin/41983627530918476/
• https://www.moodtackle.com/pin/53128940672419087/
• https://www.moodtackle.com/pin/90316284750638152/
• https://www.moodtackle.com/pin/734092618450362918/
• https://www.moodtackle.com/pin/926354081736215407/
• https://www.moodtackle.com/pin/481627093518704356/
Should not have
• should not look commercial or have cartoonish looking logos. However happy with a simple line drawing or logo with initials etc.

```html
<!DOCTYPE html>
<html lang="en">
<head>
<meta charset="utf-8">
<title>Lucy Brandt — Business Card</title>
<link rel="stylesheet" href="https://fonts.googleapis.com/css2?family=Jost:wght@300;400&display=swap">
<style>
  :root {
    --backdrop: #e6e4e0;
    --card-black: #0d0d0d;
    --card-white: #f7f7f5;
    --edge-silver: #d9d9d9;
    --ink-grey: #4a4a4a;
    --ink-light: #ffffff;
  }
  * { margin: 0; padding: 0; box-sizing: border-box; }
  html, body {
    width: 1200px;
    height: 892px;
    overflow: hidden;
    background: var(--backdrop);
    font-family: "Jost", "Futura", sans-serif;
  }
  .canvas {
    width: 1200px;
    height: 892px;
    display: flex;
    align-items: center;
    justify-content: center;
    gap: 60px;
  }
  .card {
    width: 520px;
    height: 297px;
    position: relative;
    box-shadow: 0 10px 28px rgba(0,0,0,0.18);
  }
  /* Side 1 — name */
  .card--front {
    background: var(--edge-silver);
    padding: 9px;
  }
  .card--front .face {
    width: 100%;
    height: 100%;
    background: var(--card-black);
    position: relative;
  }
  .name {
    position: absolute;
    left: 230px;
    top: 150px;
    color: var(--ink-light);
    font-weight: 400;
    line-height: 1;
  }
  .name__first {
    display: block;
    font-size: 40px;
    letter-spacing: 0.42em;
  }
  .name__last {
    display: block;
    font-size: 26px;
    letter-spacing: 0.34em;
    margin-top: 8px;
    font-weight: 300;
  }
  /* Side 2 — contact */
  .card--back {
    background: var(--card-black);
    padding: 10px;
  }
  .card--back .face {
    width: 100%;
    height: 100%;
    background: var(--card-white);
    position: relative;
    color: var(--ink-grey);
  }
  .contact {
    position: absolute;
    left: 26px;
    top: 24px;
    font-size: 14px;
    font-weight: 300;
    line-height: 1.35;
    letter-spacing: 0.02em;
  }
  .services {
    position: absolute;
    left: 26px;
    top: 92px;
    width: 440px;
    display: flex;
    justify-content: space-between;
    font-size: 13px;
    font-weight: 300;
    letter-spacing: 0.02em;
  }
  .services__divider { color: var(--card-black); }
</style>
</head>
<body>
  <main class="canvas">
    <section class="card card--front" aria-label="Card side one">
      <div class="face">
        <h1 class="name">
          <span class="name__first">Lucy</span>
          <span class="name__last">Brandt</span>
        </h1>
      </div>
    </section>

    <section class="card card--back" aria-label="Card side two">
      <div class="face">
        <p class="contact">
          <span class="contact__phone">+61 400 817 263</span><br>
          <span class="contact__email">lucy.brandt@mailnest.com.au</span>
        </p>
        <p class="services">
          <span>event management</span>
          <span class="services__divider">/</span>
          <span>brand activation</span>
          <span class="services__divider">/</span>
          <span>Advisory Services</span>
        </p>
      </div>
    </section>
  </main>
</body>
</html>
```